Re-style home page - eye-catching and unique design for social commerce website

We need a new concept design for BrinoKet's home page.
We don't want to make huge changes but creating a more professional and eye-catching style.

We need to look very serious like a professional services company and in the same time to look like a social network for e-commerce.

Our logo is very captive and you can use to creating something of harmonious.

This is a re-style and I'm excepted to see unique and fresh design like Glimmora.

Target Market(s)

e-commerce and social

Industry/Entity Type

Social

Number of Pages Required

1 page

Font styles to use
Serif
Sans Serif

Requirements
Must have
• An eye-catching result.
• Search bar with logo and Login How it works and business
• The slogan with login and signup.
• Footer links.
Nice to have
• I would like to open the home page and see only two clear ways:
• -Consumer
• --Search
• --The slogan
• --Login and Signup
• --How it works
• -Business
• --Go to Business area
• Background: City, Shopping.
Should not have
• Scrollbar style!

```html
<!DOCTYPE html>
<html lang="en">
<head>
<meta charset="utf-8">
<title>BrinoKet — Shop directly from your profile</title>
<link rel="stylesheet" href="https://fonts.googleapis.com/css2?family=Open+Sans:wght@400;600;700&family=Montserrat:wght@400;500;600&display=swap">
<style>
  :root {
    --night: #1f2150;
    --violet: #3a3470;
    --dusk: #5b4a7c;
    --header: rgba(24, 26, 66, 0.72);
    --field: rgba(255, 255, 255, 0.12);
    --white: #ffffff;
    --muted: rgba(255, 255, 255, 0.6);
    --ink: #3b3b3b;
    --grey: #a7a7a7;
    --red: #cf2a2a;
    --green: #7cb82f;
    --denim-dark: #1b2638;
    --denim: #2f4766;
    --denim-light: #56708f;
    --avatar: #c9b3a4;
  }
  * { box-sizing: border-box; margin: 0; padding: 0; }
  html, body { width: 1200px; height: 675px; overflow: hidden; }
  body {
    position: relative;
    font-family: "Montserrat", Arial, sans-serif;
    color: var(--white);
    background: var(--night);
  }
  .city-backdrop {
    position: absolute; inset: 0;
    background:
      radial-gradient(ellipse 420px 300px at 170px 300px, rgba(120, 90, 110, 0.55), transparent 70%),
      radial-gradient(ellipse 380px 320px at 1050px 240px, rgba(150, 120, 150, 0.45), transparent 70%),
      linear-gradient(180deg, #3d3a6e 0%, #4a4278 40%, #3a3568 70%, #2a2a5c 100%);
  }
  .network { position: absolute; inset: 0; }

  .site-header {
    position: absolute; top: 0; left: 0; width: 1200px; height: 59px;
    background: var(--header);
  }
  .brand {
    position: absolute; left: 26px; top: 12px;
    display: flex; align-items: center; gap: 8px;
    font-family: "Open Sans", Arial, sans-serif;
    font-weight: 700; font-size: 28px; letter-spacing: -0.5px;
    color: var(--white);
  }
  .brand-dot { width: 18px; height: 18px; border-radius: 50%; background: var(--white); }
  .search-field {
    position: absolute; left: 350px; top: 11px; width: 454px; height: 35px;
    border-radius: 3px; background: var(--field);
    font-family: "Open Sans", Arial, sans-serif; font-size: 13px;
    color: var(--muted); line-height: 35px; padding-left: 17px;
  }
  .search-icon { position: absolute; left: 816px; top: 19px; }
  .login-link {
    position: absolute; left: 871px; top: 20px;
    font-size: 13px; font-weight: 500; color: var(--white);
  }

  .feed-card {
    position: absolute; left: 350px; top: 144px; width: 500px; height: 371px;
    border-radius: 5px; overflow: hidden;
  }
  .card-photo {
    position: absolute; inset: 0;
    background:
      radial-gradient(ellipse 260px 180px at 180px 120px, var(--denim-light), transparent 75%),
      radial-gradient(ellipse 300px 200px at 330px 300px, var(--denim), transparent 75%),
      linear-gradient(160deg, var(--denim) 0%, var(--denim-dark) 100%);
  }
  .card-shade { position: absolute; inset: 0; background: rgba(20, 26, 40, 0.35); }
  .card-body { position: relative; text-align: center; }
  .card-title {
    font-family: "Open Sans", Arial, sans-serif; font-weight: 600;
    font-size: 25px; margin-top: 33px; line-height: 32px;
  }
  .card-subtitle {
    font-family: "Open Sans", Arial, sans-serif; font-weight: 600;
    font-size: 16px; margin-top: 17px; line-height: 20px;
  }
  .feed-form { width: 202px; margin: 13px auto 0; }
  .select {
    position: relative; height: 32px; border-radius: 3px; background: var(--white);
    color: var(--ink); font-size: 12px; text-align: left; line-height: 32px;
    padding-left: 14px; margin-bottom: 6px;
  }
  .select.with-pin { padding-left: 31px; }
  .select .pin { position: absolute; left: 14px; top: 9px; }
  .select .chevron { position: absolute; right: 13px; top: 13px; }
  .btn {
    display: block; height: 32px; border-radius: 3px; line-height: 32px;
    font-size: 13px; font-weight: 500; color: var(--white); text-align: center;
  }
  .btn-signup { background: var(--red); margin-top: 5px; }
  .divider { height: 1px; background: rgba(255,255,255,0.45); margin: 23px 0 20px; }
  .btn-business { background: var(--green); }
  .btn-business svg { vertical-align: middle; margin-left: 6px; }
  .how-link { display: block; margin-top: 14px; font-size: 12px; font-weight: 500; }

  .site-footer { position: absolute; left: 0; top: 582px; width: 1200px; text-align: center; }
  .footer-links { display: flex; justify-content: center; gap: 26px; font-size: 11.5px; font-weight: 500; padding-left: 8px; }
  .copyright { margin-top: 11px; font-size: 9.5px; font-weight: 500; }
</style>
</head>
<body>
  <div class="city-backdrop" role="img" aria-label="Busy city shopping street with shoppers, dimmed under a violet tint"></div>

  <svg class="network" width="1200" height="675" viewBox="0 0 1200 675">
    <g fill="none" stroke="#ffffff" stroke-opacity="0.6" stroke-width="1.5" stroke-dasharray="1.5 3" stroke-linecap="round">
      <path d="M351 116 Q360 140 390 144"/>
      <path d="M415 120 Q410 140 420 144"/>
      <path d="M474 123 Q465 140 450 144"/>
      <path d="M309 177 Q320 200 350 204"/>
      <path d="M694 130 Q700 140 702 144"/>
      <path d="M756 113 Q770 130 775 144"/>
      <path d="M808 134 Q820 140 830 144"/>
      <path d="M869 158 Q865 180 850 186"/>
      <path d="M302 399 Q315 410 350 412"/>
      <path d="M298 472 Q310 448 350 450"/>
      <path d="M365 522 Q385 520 395 515"/>
      <path d="M895 410 Q880 435 850 434"/>
      <path d="M915 471 Q890 470 850 464"/>
      <path d="M872 510 Q858 500 840 515"/>
      <path d="M799 525 Q795 520 790 515"/>
    </g>
    <g fill="var(--avatar)" stroke="#ffffff" stroke-width="2.5">
      <circle cx="351" cy="101" r="15" role="img" aria-label="Member portrait"/>
      <circle cx="415" cy="105" r="15" role="img" aria-label="Member portrait"/>
      <circle cx="474" cy="108" r="15" role="img" aria-label="Member portrait"/>
      <circle cx="309" cy="162" r="15" role="img" aria-label="Member portrait"/>
      <circle cx="694" cy="115" r="15" role="img" aria-label="Member portrait"/>
      <circle cx="756" cy="98" r="15" role="img" aria-label="Member portrait"/>
      <circle cx="808" cy="119" r="15" role="img" aria-label="Member portrait"/>
      <circle cx="869" cy="143" r="15" role="img" aria-label="Member portrait"/>
      <circle cx="302" cy="384" r="15" role="img" aria-label="Member portrait"/>
      <circle cx="298" cy="487" r="15" role="img" aria-label="Member portrait"/>
      <circle cx="365" cy="537" r="15" role="img" aria-label="Member portrait"/>
      <circle cx="895" cy="395" r="15" role="img" aria-label="Member portrait"/>
      <circle cx="915" cy="456" r="15" role="img" aria-label="Member portrait"/>
      <circle cx="872" cy="525" r="15" role="img" aria-label="Member portrait"/>
      <circle cx="799" cy="540" r="15" role="img" aria-label="Member portrait"/>
    </g>
  </svg>

  <header class="site-header">
    <div class="brand"><span>BrinoKet</span><span class="brand-dot"></span></div>
    <div class="search-field">Search keyword</div>
    <svg class="search-icon" width="20" height="20" viewBox="0 0 20 20">
      <circle cx="8" cy="8" r="6" fill="none" stroke="#ffffff" stroke-width="2.6"/>
      <line x1="12.5" y1="12.5" x2="18" y2="18" stroke="#ffffff" stroke-width="2.8" stroke-linecap="round"/>
    </svg>
    <span class="login-link">Login</span>
  </header>

  <main class="feed-card">
    <div class="card-photo" role="img" aria-label="Close-up of folded blue denim jeans"></div>
    <div class="card-shade"></div>
    <div class="card-body">
      <h1 class="card-title">Shop directly from your profile</h1>
      <h2 class="card-subtitle">Setup your feed</h2>
      <div class="feed-form">
        <div class="select">Active life
          <svg class="chevron" width="12" height="7" viewBox="0 0 12 7"><path d="M1 1l5 5 5-5" fill="none" stroke="#b5b5b5" stroke-width="1.4"/></svg>
        </div>
        <div class="select with-pin">
          <svg class="pin" width="10" height="14" viewBox="0 0 10 14"><path d="M5 0a5 5 0 0 0-5 5c0 3.6 5 9 5 9s5-5.4 5-9a5 5 0 0 0-5-5zm0 7a2 2 0 1 1 0-4 2 2 0 0 1 0 4z" fill="var(--grey)"/></svg>
          London
          <svg class="chevron" width="12" height="7" viewBox="0 0 12 7"><path d="M1 1l5 5 5-5" fill="none" stroke="#b5b5b5" stroke-width="1.4"/></svg>
        </div>
        <a class="btn btn-signup">Sign Up</a>
        <div class="divider"></div>
        <a class="btn btn-business">Go to Business Area<svg width="17" height="7" viewBox="0 0 17 7"><path d="M0 3.5h15M12 0.8l3.5 2.7L12 6.2" fill="none" stroke="#ffffff" stroke-width="1"/></svg></a>
        <a class="how-link">How it works</a>
      </div>
    </div>
  </main>

  <footer class="site-footer">
    <nav class="footer-links">
      <span>About Us</span><span>Blog</span><span>Business</span><span>Jobs</span><span>Privacy</span><span>FAQ</span><span>Contacts</span>
    </nav>
    <p class="copyright">© 2015 BrinoKet. All right reserved.</p>
  </footer>
</body>
</html>
```